Flyer for Medical practice welcoming new patients

We need a DL size brochure designed for Medical practice to advertise that we are accepting new patients. Our practice has special interests in women's and children's health and seniors health. Our existing advertising materials are in the colour scheme of purples I have uploaded our logo which includes our colour scheme.

Target Market(s)

Versatile to target anyone looking for a small medical practice that offers continuous care of seeing the same Doctor every time

Industry/Entity Type

Advertising

Font styles to use
Serif

Colors
6b449b
876aae
b7a5cc

Requirements
Must have
• The practice logo of just the picture not Dr Petra Holcombe.
• Purple colour scheme.
• Practice name: Tarrabeen Medical Practice.
• Address: 147 Corlett Rd, Tarrabeen NSW 2500.
• Phone: 4871 6035.
• DL size brochure
• Welcoming new patients ( a strong emphasis needs to be placed on this)
• Nurse and onsite ECG's and lung function tests.
• Travel vaccines including yellow fever
• Bulk billing for tertiary students
• We would also like design to alter the text so that we can change the points to be reflect who we are targeting at the time.
Nice to have
• The practice logo with Dr Petra Holcombe somewhere not as a feature as the practice no longer goes under this name but is still well known as Dr Holcombe's.

```html
<!DOCTYPE html>
<html lang="en">
<head>
<meta charset="utf-8">
<title>Tarrabeen Medical Practice – Accepting New Patients</title>
<link href="https://fonts.googleapis.com/css2?family=Open+Sans:wght@400;600&family=Roboto+Condensed:wght@700&family=Carlito&family=Arimo:wght@400;700&display=swap" rel="stylesheet">
<style>
  :root {
    --purple-deep: #6b449b;
    --purple-mid: #876aae;
    --purple-soft: #b7a5cc;
    --purple-pale: #e4d6ea;
    --lilac-wash: #d3c8e2;
    --white: #ffffff;
    --backdrop: #d9d9d9;
  }
  * { margin: 0; padding: 0; box-sizing: border-box; }
  html, body {
    width: 1200px; height: 1000px; overflow: hidden;
    background: var(--backdrop);
  }
  .flyer {
    position: absolute; left: 347px; top: 30px;
    width: 440px; height: 925px; overflow: hidden;
    background: var(--white);
  }
  .flyer-shapes { position: absolute; inset: 0; }
  .practice-mark {
    position: absolute; left: 208px; top: 20px;
    width: 158px; height: 158px; border-radius: 50%;
    border: 4px solid var(--purple-pale);
  }
  .practice-name {
    position: absolute; left: 140px; top: 186px; width: 290px;
    text-align: center;
    font-family: "Open Sans", sans-serif; font-weight: 600;
    font-size: 25px; line-height: 31px; color: var(--purple-deep);
  }
  .headline {
    position: absolute; left: 20px; top: 322px; width: 360px;
    text-align: center; color: var(--purple-deep);
  }
  .headline-lead {
    font-family: "Arimo", sans-serif; font-size: 25px;
    letter-spacing: 6px; line-height: 30px;
  }
  .headline-main {
    font-family: "Roboto Condensed", sans-serif; font-weight: 700;
    font-size: 42px; line-height: 44px; letter-spacing: -0.5px;
  }
  .headline-big {
    font-family: "Roboto Condensed", sans-serif; font-weight: 700;
    font-size: 76px; line-height: 74px; letter-spacing: 1px;
  }
  .services {
    position: absolute; left: 10px; top: 634px; width: 420px;
    list-style: none;
    font-family: "Carlito", sans-serif; font-size: 20px; line-height: 27px;
    color: var(--white);
  }
  .services li { position: relative; padding-left: 16px; margin-bottom: 13px; }
  .services li::before {
    content: ""; position: absolute; left: 1px; top: 9px;
    width: 10px; height: 10px; border-radius: 50%; background: var(--white);
  }
  .contact {
    position: absolute; left: 9px; top: 843px;
    font-family: "Arimo", sans-serif; font-size: 15.5px; line-height: 24px;
    color: var(--white);
  }
  .contact-title { color: var(--purple-deep); font-weight: 700; letter-spacing: 0.6px; }
  .contact-label { font-weight: 700; }
</style>
</head>
<body>
<main class="flyer">
  <svg class="flyer-shapes" width="440" height="925" viewBox="0 0 440 925" aria-hidden="true">
    <defs>
      <linearGradient id="lowerPanel" x1="0" y1="0" x2="0.3" y2="1">
        <stop offset="0" stop-color="#7b5aa8"/>
        <stop offset="1" stop-color="#ad9aca"/>
      </linearGradient>
      <linearGradient id="ovalWash" x1="0" y1="0" x2="0" y2="1">
        <stop offset="0.3" stop-color="#ffffff"/>
        <stop offset="1" stop-color="#d1c5e0"/>
      </linearGradient>
    </defs>
    <rect class="lower-panel" width="440" height="925" fill="url(#lowerPanel)"/>
    <path class="light-facet" d="M440 660 L230 835 L440 925 Z" fill="#ffffff" opacity="0.12"/>
    <path class="soft-band" d="M0 0 L123 0 C60 90 18 210 0 330 Z" fill="var(--purple-soft)"/>
    <path class="deep-band" d="M118 0 L181 0 C100 100 35 250 28 400 L8 470 C0 420 0 380 0 330 C18 210 60 90 118 0 Z" fill="var(--purple-deep)"/>
    <path class="welcome-oval" d="M181 0 L440 0 L440 445 C400 560 310 630 210 620 C100 605 25 520 28 400 C32 250 100 100 181 0 Z" fill="url(#ovalWash)"/>
  </svg>

  <div class="practice-mark"></div>
  <p class="practice-name">Tarrabeen<br>Medical Practice</p>

  <h1 class="headline">
    <span class="headline-lead">WE ARE NOW</span><br>
    <span class="headline-main">ACCEPTING NEW</span><br>
    <span class="headline-big">PATIENTS!</span>
  </h1>

  <ul class="services">
    <li>Nurse on site for ECG's, lung function tests, health assessments and much more</li>
    <li>We offer travel vaccines including<br>yellow fever</li>
    <li>Bulk billing for tertiary<br>students</li>
  </ul>

  <div class="contact">
    <p class="contact-title">CONTACT DETAILS:</p>
    <p><span class="contact-label">Address:</span> 147 Corlett Rd, Tarrabeen NSW 2500</p>
    <p><span class="contact-label">Telephone:</span> 4871 6035</p>
  </div>
</main>
</body>
</html>
```